Stationary design for boutique production house

We need a stationary design for our production house, 'Lorno Productions' based in Singapore. We produce microfilms as well as podcasts, talkshows and events. Our logo is a stylized icon of our director, who is also the executive producer and host of our programs, Lorno. Our main company colors are Red, Black and white. We would like a clean, minimalist design incorporating our existing company logo that conveys a sense of urbanism and elegance.

Logo and font files are attached. f

Target Market(s)

We focus on lifestyle media rather than entertainment.

Industry/Entity Type

Boutique

Font styles to use
Serif
Sans Serif

Colors
ec1f27
ffffff
000000

Requirements
Must have
• Our company logo and at least one of our company colors.
Nice to have
• Our address and contact information.
Should not have
• Changes made to the company logo (using only certain parts of it is fine though)

```html
<!DOCTYPE html>
<html lang="en">
<head>
<meta charset="utf-8">
<title>Lorno Productions – Business Cards</title>
<link href="https://fonts.googleapis.com/css2?family=Jost:wght@400;500&display=swap" rel="stylesheet">
<style>
  :root {
    --brand-red: #db1b24;
    --ink: #1e1e1e;
    --paper: #ffffff;
    --stage: #e9e9e9;
    --card-shadow: rgba(0, 0, 0, 0.18);
  }
  html, body {
    margin: 0;
    padding: 0;
    overflow: hidden;
  }
  .canvas {
    width: 1200px;
    height: 659px;
    background: var(--stage);
    display: flex;
    align-items: center;
    justify-content: center;
    gap: 80px;
    font-family: "Jost", "Futura", sans-serif;
  }
  .card {
    width: 300px;
    height: 510px;
    box-sizing: border-box;
    box-shadow: 0 6px 20px var(--card-shadow);
    display: flex;
    flex-direction: column;
    align-items: center;
  }
  .card--back {
    background: var(--brand-red);
    color: var(--paper);
    padding-top: 150px;
    text-align: center;
  }
  .card--front {
    background: var(--paper);
    justify-content: center;
  }
  .wordmark {
    display: flex;
    align-items: center;
    gap: 8px;
    font-weight: 500;
    letter-spacing: 0.06em;
    text-transform: uppercase;
  }
  .wordmark__dot {
    border-radius: 50%;
    flex: none;
  }
  .card--back .wordmark {
    font-size: 13px;
    color: var(--paper);
  }
  .card--back .wordmark__dot {
    width: 9px;
    height: 9px;
    background: var(--paper);
  }
  .card--front .wordmark {
    font-size: 22px;
    color: var(--ink);
  }
  .card--front .wordmark__dot {
    width: 14px;
    height: 14px;
    background: var(--brand-red);
  }
  .person {
    margin-top: 14px;
    line-height: 1.1;
  }
  .person__name {
    font-size: 19px;
    font-weight: 500;
    letter-spacing: 0.04em;
    text-transform: uppercase;
  }
  .person__role {
    font-size: 14px;
    letter-spacing: 0.04em;
    text-transform: uppercase;
  }
  .address {
    margin-top: 14px;
    font-size: 13px;
    font-style: normal;
    line-height: 1.35;
  }
  .contacts {
    list-style: none;
    margin: 8px 0 0;
    padding: 0;
    font-size: 13px;
    line-height: 1.55;
  }
  .contacts li {
    display: flex;
    align-items: center;
    justify-content: center;
    gap: 7px;
  }
  .contacts svg {
    width: 11px;
    height: 11px;
    fill: var(--paper);
    flex: none;
  }
</style>
</head>
<body>
<main class="canvas">
  <section class="card card--back">
    <div class="wordmark"><span class="wordmark__dot"></span>Lorno Productions</div>
    <div class="person">
      <div class="person__name">Mara Quint</div>
      <div class="person__role">CEO/Founder</div>
    </div>
    <address class="address">412 Willow Court<br>Harbor City, Oregon 20817</address>
    <ul class="contacts">
      <li>
        <svg viewBox="0 0 12 12" aria-hidden="true"><path d="M2.5 0.8l2 2-1 1.3c0.6 1.4 1.9 2.8 3.4 3.4l1.3-1 2 2-1.4 1.9C5.1 10.2 1.8 6.9 0.6 2.2z"/></svg>
        614 205 7781
      </li>
      <li>
        <svg viewBox="0 0 12 12" aria-hidden="true"><path d="M3 0h6v12H3zM4 1.5v8h4v-8z"/></svg>
        742 319 5026
      </li>
      <li>
        <svg viewBox="0 0 12 12" aria-hidden="true"><path d="M3 0h5v3H3zM0 4h12v6h-2v2H2v-2H0zM3 8v3h6V8z"/></svg>
        358 640 2197
      </li>
      <li>
        <svg viewBox="0 0 12 12" aria-hidden="true"><path d="M0 2h12v8H0zM1.2 3l4.8 3.6L10.8 3z"/></svg>
        hello@lornostudio.com
      </li>
      <li>
        <svg viewBox="0 0 12 12" aria-hidden="true"><path d="M6 0a6 6 0 1 0 0 12A6 6 0 0 0 6 0zm0 1.2c.8 1 1.3 2.6 1.3 4.8S6.8 9.8 6 10.8c-.8-1-1.3-2.6-1.3-4.8S5.2 2.2 6 1.2z"/></svg>
        www.lornostudio.com
      </li>
    </ul>
  </section>

  <section class="card card--front">
    <div class="wordmark"><span class="wordmark__dot"></span>Lorno Productions</div>
  </section>
</main>
</body>
</html>
```